Business cards to launch an education platform

Hi,
I am looking at having new business cards designed.
I am a startup, developing a web platform for schools and university, the education world. It's an online assessment system.
I would like a card that looks classy, and that is using the colors and the font of my logo.

I have attached:
1) my logo
2) A business card that I have designed quickly so you can have all the information required in the card, but I really don't like it.
3) The font that I am using (Lato Regular) to design my web platform
4) Some screenshots of my web platform so you can have a look at the style that I have.

Target Market(s)

Major market: Education system: Schools and university
Minor markets: Business in general

Industry/Entity Type

Business

Contact Information for Business Card

Clara Fenwick
Director

M: 0437 518 902
E: clara.fenwick@amberLoomSystems.com.au

Requirements
Must have
• The colors of my logo

```html
<!DOCTYPE html>
<html lang="en">
<head>
<meta charset="UTF-8">
<title>Amber Loom Systems – Business Cards</title>
<link rel="stylesheet" href="https://fonts.googleapis.com/css2?family=Lato:wght@400;700&display=swap">
<style>
  :root {
    --bg: #e9ebee;
    --navy: #1d3f86;
    --blue-deep: #1470b8;
    --blue-mid: #1f8fd2;
    --blue-light: #2fb0e0;
    --white: #ffffff;
    --pale-1: #e4e6f1;
    --pale-2: #f3f5fa;
    --pale-3: #e3eef8;
    --shadow: rgba(20, 40, 80, 0.18);
  }
  * { box-sizing: border-box; margin: 0; padding: 0; }
  html, body {
    width: 1200px; height: 900px; overflow: hidden;
    background: var(--bg);
    font-family: "Lato", Arial, sans-serif;
  }
  .stage {
    width: 1200px; height: 900px;
    display: flex; flex-direction: column;
    align-items: center; justify-content: center; gap: 40px;
  }
  .card {
    position: relative;
    width: 560px; height: 342px;
    border-radius: 4px;
    overflow: hidden;
    box-shadow: 0 8px 24px var(--shadow);
    background: var(--white);
  }
  .brand {
    position: absolute;
    display: flex; align-items: center; gap: 14px;
  }
  .brand-mark {
    width: 44px; height: 44px;
    background: var(--navy);
  }
  .brand-name {
    color: var(--navy);
    font-weight: 400;
    font-size: 27px;
    letter-spacing: 3px;
    text-transform: uppercase;
    line-height: 1;
  }

  /* Back of card */
  .card-back .backdrop {
    position: absolute; inset: 0;
    background: linear-gradient(120deg, var(--pale-1) 0%, var(--pale-2) 50%, var(--pale-3) 100%);
  }
  .card-back .brand {
    left: 50%; top: 50%;
    transform: translate(-50%, -50%);
  }

  /* Front of card */
  .card-front .waves { position: absolute; inset: 0; }
  .card-front .brand { left: 118px; top: 48px; }
  .contact {
    position: absolute;
    left: 0; right: 0; top: 236px;
    text-align: center;
    color: var(--white);
  }
  .contact-name { font-size: 21px; font-weight: 400; line-height: 1.1; }
  .contact-role { font-size: 13px; margin-top: 2px; }
  .contact-line {
    display: flex; align-items: center; justify-content: center; gap: 7px;
    font-size: 14px; margin-top: 8px;
  }
  .contact-line svg { width: 12px; height: 12px; fill: var(--white); }
  .contact-line + .contact-line { margin-top: 4px; }
</style>
</head>
<body>
<main class="stage">

  <section class="card card-back">
    <div class="backdrop" role="img" aria-label="Soft pale lavender and light blue background with faint large brand decoration"></div>
    <div class="brand">
      <span class="brand-mark"></span>
      <span class="brand-name">Amber Loom Systems</span>
    </div>
  </section>

  <section class="card card-front">
    <svg class="waves" viewBox="0 0 560 342" preserveAspectRatio="none">
      <defs>
        <linearGradient id="front-fill" x1="0" y1="0" x2="0" y2="1">
          <stop offset="0" stop-color="#2fb0e0"/>
          <stop offset="1" stop-color="#1577c4"/>
        </linearGradient>
      </defs>
      <rect width="560" height="342" fill="url(#front-fill)"/>
      <path d="M0 112 C130 205 340 245 560 212 V236 C340 266 120 225 0 132 Z" fill="#1470b8"/>
      <path d="M0 0 H560 V198 C340 232 140 196 0 98 Z" fill="#ffffff"/>
      <path d="M150 158 C260 215 400 228 560 205" fill="none" stroke="#1f8fd2" stroke-width="3"/>
    </svg>
    <div class="brand">
      <span class="brand-mark"></span>
      <span class="brand-name">Amber Loom Systems</span>
    </div>
    <div class="contact">
      <p class="contact-name">Clara Fenwick</p>
      <p class="contact-role">Director</p>
      <p class="contact-line">
        <svg viewBox="0 0 24 24"><path d="M6.6 10.8a15.1 15.1 0 0 0 6.6 6.6l2.2-2.2a1 1 0 0 1 1-.25 11.4 11.4 0 0 0 3.6.57 1 1 0 0 1 1 1V20a1 1 0 0 1-1 1A17 17 0 0 1 3 4a1 1 0 0 1 1-1h3.5a1 1 0 0 1 1 1c0 1.25.2 2.45.57 3.57a1 1 0 0 1-.25 1z"/></svg>
        0437 518 902
      </p>
      <p class="contact-line">
        <svg viewBox="0 0 24 24"><path d="M2 5h20v14H2z M2 5l10 8 10-8" fill="none" stroke="#ffffff" stroke-width="2"/></svg>
        clara.fenwick@amberLoomSystems.com.au
      </p>
    </div>
  </section>

</main>
</body>
</html>
```